Christian Media Company Website

I am looking to design an easy to follow, sleek, creative website for my Christian video Bible study platform. On this platform you will be able to sign up to have access to dozens of free high-quality video Bible studies. With that being said There will be a total of 3 pages needed.

First, I will need the home page. This should contain all critical information to inform the customer. The design should be easy to follow, professional, and creative. I will post to some websites I like, if you just copy the website in your design will be removed immediately.

Secondly, we will need a landing Bible study page for people to look through the Bible studies to select one. I have uploaded Study images below with the aspect ratio I want for the design (for each Bible study image). There should be 2 sections Topical studies and Doctrinal Studies (with series under each section). I would like for people to be able to slide left or right through the studies under each category.

Lastly, we will need a video series page. This page needs to have the video they are watching, a playlist of the other videos, as well as a place to put the speaker's image and description. We will have studies that they can download so please make a place for this.

I will upload our color in the files along with our logo! Looking forward to seeing what you all will come up with!

Websites I like :
https://lanternvale.org/
https://www.quillharborfilms.org/
https://www.dunmorel.com/
https://tessavint.org/

Target Market(s)

Christians

Industry/Entity Type

Christian Video Design

Coding

Coded - Design and coding required

Number of Pages Required

3 page

Font styles to use
Sans Serif

Colors
00AB8E
00BBA5
67D7C9
C6EFE9
E9F9F6

Requirements
Should not have
• Pre-Used Templates

```html
<!DOCTYPE html>
<html lang="en">
<head>
<meta charset="utf-8">
<title>Harvest Path — Video Bible Studies</title>
<link href="https://fonts.googleapis.com/css2?family=Poppins:wght@400;500;600;700&display=swap" rel="stylesheet">
<style>
:root{
  --teal:#00AB8E;
  --teal-2:#00BBA5;
  --teal-3:#67D7C9;
  --teal-4:#C6EFE9;
  --teal-5:#E9F9F6;
  --ink:#222222;
  --text:#333333;
  --muted:#666666;
  --white:#ffffff;
  --black:#050505;
}
*{box-sizing:border-box;margin:0;padding:0}
html,body{width:1200px;height:3791px;overflow:hidden}
body{position:relative;font-family:'Poppins',sans-serif;color:var(--text);background:var(--white)}
.abs{position:absolute}
a{color:inherit;text-decoration:none}

/* header */
.site-header{position:absolute;left:0;top:0;width:1200px;height:82px;background:var(--white);z-index:5}
.brand{position:absolute;left:90px;top:17px;display:flex;align-items:center;gap:10px}
.brand-mark{width:22px;height:22px;background:var(--teal)}
.brand-name{font-weight:600;font-size:23px;line-height:28px;color:var(--teal);text-transform:uppercase}
.main-nav{position:absolute;left:357px;top:36px;display:flex;gap:32px;font-size:13px;font-weight:500;color:var(--ink)}
.btn{display:inline-flex;align-items:center;justify-content:center;border-radius:30px;font-weight:600;text-transform:uppercase}
.btn-signup{position:absolute;left:973px;top:22px;width:137px;height:46px;background:var(--teal);color:var(--white);font-size:15px}

/* hero */
.hero{position:absolute;left:0;top:82px;width:1200px;height:640px}
.hero-photo{position:absolute;inset:0;background:linear-gradient(100deg,#5c6a78 0%,#9aa7b3 25%,#d9dcdc 45%,#f1f1ef 70%,#e4e6e6 100%);clip-path:polygon(0 0,1200px 0,1200px 544px,600px 633px,0 544px)}
.hero-curve{position:absolute;left:0;top:0}
.hero-copy{position:absolute;left:628px;top:175px;width:450px}
.hero-title{font-size:47px;line-height:54px;font-weight:600;color:#2a2a2a;text-transform:uppercase}
.hero-text{margin-top:22px;font-size:12.5px;line-height:24px;color:#444}
.btn-start{margin-top:24px;width:170px;height:46px;background:var(--teal);color:var(--white);font-size:15px}
.hero-dots{position:absolute;left:570px;top:573px;display:flex;gap:5px}
.hero-dots span{width:11px;height:11px;border-radius:50%;background:#c4c4c4}
.hero-dots span:first-child{background:var(--white)}

/* section titles */
.section-title{position:absolute;left:0;width:1200px;text-align:center;font-size:31px;font-weight:600;color:var(--ink);text-transform:uppercase}
.section-title::after{content:"";display:block;width:40px;height:3px;background:var(--teal);margin:10px auto 0}

/* series */
.series-card{position:absolute;width:305px;height:241px;border-radius:6px;overflow:hidden;display:flex;align-items:flex-end;justify-content:center}
.series-label{font-size:23px;font-weight:600;color:var(--white);text-transform:uppercase;margin-bottom:34px;text-shadow:0 1px 3px rgba(0,0,0,.4)}
.card-play{position:absolute;left:138px;top:100px}
.card-top{position:absolute;top:28px;left:0;width:100%;text-align:center;font-size:23px;font-weight:600;color:var(--white);text-transform:uppercase}
.speaker-bar{position:absolute;left:0;bottom:0;width:100%;height:50px;background:var(--teal);display:flex;align-items:center;padding:0 10px}
.speaker-avatar{width:38px;height:38px;border-radius:50%;background:#c9b9a6;border:2px solid var(--white)}
.speaker-info{margin-left:12px;color:var(--white);font-size:11px;font-weight:600;line-height:14px;text-transform:uppercase}
.speaker-info small{display:block;font-size:9px;font-weight:500;text-transform:none}
.btn-download{margin-left:auto;width:118px;height:36px;background:var(--white);color:var(--teal);font-size:12px}

/* band */
.everyone{position:absolute;left:0;top:1708px;width:1200px;height:366px;background:radial-gradient(ellipse at 60% 70%,#1bc2a6 0%,var(--teal-2) 45%,var(--teal) 100%);text-align:center;color:var(--white)}
.everyone h2{margin-top:70px;font-size:31px;font-weight:600;text-transform:uppercase}
.everyone h2::after{content:"";display:block;width:40px;height:3px;background:var(--white);margin:10px auto 0}
.everyone p{width:900px;margin:20px auto 0;font-size:12.5px;line-height:24px}
.band-actions{margin-top:26px;display:flex;justify-content:center;gap:14px}
.btn-topical{width:170px;height:46px;background:var(--white);color:var(--teal);font-size:15px}
.btn-doctrinal{width:195px;height:46px;border:2px solid var(--white);color:var(--white);font-size:15px}

/* blog */
.blog-tile{position:absolute}
.blog-post{position:absolute;left:457px;top:2240px;width:290px}
.blog-post h3{font-size:15.5px;font-weight:600;line-height:24px;color:var(--ink)}
.blog-post p{margin-top:10px;font-size:12.5px;line-height:24px;color:#444}
.learn-more{display:inline-block;margin-top:10px;font-size:13px;font-weight:600;color:var(--teal);border-bottom:2px solid var(--teal);text-transform:uppercase}

/* contact */
.contact{position:absolute;left:0;top:2785px;width:1200px;height:545px;background:linear-gradient(180deg,#f3f3f1 0%,#ecebe6 100%)}
.field{position:absolute;border:1px solid #999;background:var(--white);border-radius:3px;font-size:11.5px;color:#444;padding:14px 16px}
.btn-submit{position:absolute;left:515px;top:3185px;width:170px;height:47px;background:var(--teal);color:var(--white);font-size:15px}

/* footer */
.footer-shape{position:absolute;left:0;top:3228px}
.footer-links{position:absolute;left:133px;top:3410px;color:var(--white)}
.footer-links h4{font-size:19px;font-weight:600;margin-bottom:14px}
.footer-links li{list-style:none;font-size:13px;line-height:33px}
.footer-divider{position:absolute;width:1px;height:300px;top:3380px;background:#333}
.footer-brand{position:absolute;left:358px;top:3412px;display:flex;align-items:center;gap:14px}
.footer-brand .brand-mark{width:30px;height:30px;background:var(--white)}
.footer-brand .brand-name{color:var(--white);font-size:35px;line-height:42px;font-weight:600}
.subscribe-input{position:absolute;left:350px;top:3530px;width:344px;height:47px;border-radius:30px;background:var(--white);font-size:12.5px;color:#555;display:flex;align-items:center;justify-content:center}
.btn-subscribe{position:absolute;left:438px;top:3601px;width:169px;height:47px;background:var(--teal);color:var(--white);font-size:16px}
.footer-contact{position:absolute;left:770px;top:3403px;width:290px;color:var(--white);font-size:12.5px;line-height:25px}
.contact-row{display:flex;gap:12px;margin-top:10px}
.contact-row svg{flex:none;margin-top:6px}
.footer-rule{position:absolute;left:142px;top:3692px;width:915px;height:1px;background:#444}
.footer-bottom{position:absolute;top:3717px;font-size:12.5px;color:var(--white)}
</style>
</head>
<body>

<header class="site-header">
  <div class="brand"><span class="brand-mark"></span><span class="brand-name">Harvest Path</span></div>
  <nav class="main-nav">
    <a>Home</a><a>ABOUT US</a><a>TABLE OF CONTENTS</a><a>REFERENCES</a><a>CONTACT</a><a>BLOG</a>
  </nav>
  <a class="btn btn-signup">Sign Up</a>
</header>

<section class="hero">
  <div class="hero-photo" role="img" aria-label="Photo of a woman praying with folded hands at a desk beside a laptop and a Bible"></div>
  <svg class="hero-curve" width="1200" height="640" viewBox="0 0 1200 640">
    <polygon points="0,544 600,633 1200,544 1200,640 0,640" fill="#ffffff"/>
    <path d="M0 544 Q300 596 600 633 Q900 590 1200 544" fill="none" stroke="#00AB8E" stroke-width="5"/>
  </svg>
  <div class="hero-copy">
    <h1 class="hero-title">Welcome to<br>Harvest Path</h1>
    <p class="hero-text">Lorem ipsum dolor sit amet, consectetur adipiscing elit, sed do eius mod tempor incididunt ut labore et dolore magna aliqua. Ut enim ad minim veniam, quis nostrud exercitation ullamc.</p>
    <a class="btn btn-start">Get Started</a>
  </div>
  <div class="hero-dots"><span></span><span></span><span></span><span></span></div>
</section>

<h2 class="section-title" style="top:785px">Our Series</h2>

<div class="series-card" style="left:126px;top:865px;background:linear-gradient(160deg,#9ea58a,#6f6a58 55%,#3a3530)" role="img" aria-label="Portrait photo of a smiling woman outdoors"><span class="series-label">All The Things Series</span></div>
<div class="series-card" style="left:447px;top:865px;background:linear-gradient(160deg,#4fd0b8,#1da98f 60%,#137d6a)" role="img" aria-label="Video thumbnail of a crown of thorns and nails, tinted teal">
  <span class="card-top">Three Gospels</span>
  <svg class="card-play" width="32" height="38" viewBox="0 0 32 38"><polygon points="0,0 32,19 0,38" fill="#fff"/></svg>
  <div class="speaker-bar">
    <span class="speaker-avatar"></span>
    <span class="speaker-info">Aaron Vale<small>Lorem ipsum dolor</small></span>
    <a class="btn btn-download">Download</a>
  </div>
</div>
<div class="series-card" style="left:768px;top:865px;background:linear-gradient(160deg,#6b6f72,#a8a9a6 55%,#d1d0cb)" role="img" aria-label="Photo of a man looking at the sea behind large faint words"><span class="series-label">God's Design Website</span></div>

<div class="series-card" style="left:126px;top:1130px;background:linear-gradient(180deg,#4c3f6a,#c7546a 45%,#f2a45b 65%,#3b2220)" role="img" aria-label="Photo of three crosses on a hill at a fiery sunset"><span class="series-label">Revelation</span></div>
<div class="series-card" style="left:447px;top:1130px;background:linear-gradient(180deg,#2c3f6e,#7a6b9a 40%,#e3a06a 65%,#2a1e1b)" role="img" aria-label="Photo of three crosses on a rocky hill at dusk"><span class="series-label">Genesis &amp; Job</span></div>
<div class="series-card" style="left:768px;top:1130px;background:linear-gradient(160deg,#1d3c4e,#6d8a82 45%,#e5b35a 70%,#5b4a2c)" role="img" aria-label="Photo of a manger under a bright star with crosses on a distant hill"><span class="series-label">Promised Land</span></div>

<div class="series-card" style="left:126px;top:1392px;background:radial-gradient(ellipse at 50% 35%,#e8dcc8,#9a6a4a 40%,#4a2b1e)" role="img" aria-label="Photo of a man with raised arms at the top of stone stairs in a tunnel"><span class="series-label">James</span></div>
<div class="series-card" style="left:447px;top:1392px;background:radial-gradient(ellipse at 25% 30%,#e9b060,#7a4a24 40%,#2a1a10)" role="img" aria-label="Photo of a lit candle beside an old scroll"><span class="series-label">Paul's Letters</span></div>
<div class="series-card" style="left:768px;top:1392px;background:linear-gradient(160deg,#d6d0c6,#b3a89a 50%,#8c7660)" role="img" aria-label="Painted image of a quill and a rolled letter on old paper"><span class="series-label">Other Letters</span></div>

<section class="everyone" role="region" aria-label="Teal photo band of hands in prayer">
  <h2>Something For Everyone</h2>
  <p>Lorem ipsum dolor sit amet, consectetur adipiscing elit, sed do eiusmod tempor incididunt ut labore et dolore magna aliqua. Ut enim ad minim veniam, quis nostrud exercitation ullamco laboris nisi ut aliquip ex ea commodo consequat. Duis aute irure dolor in reprehenderit in voluptate velit esse cillum dolore eu fugiat nulla pariatur. Excepteur sint occaecat cupidatat non proident, sunt in culpa qui officia deserunt mollit anim id est laborum.</p>
  <div class="band-actions">
    <a class="btn btn-topical">Topical Studies</a>
    <a class="btn btn-doctrinal">Doctrinal Studies</a>
  </div>
</section>

<h2 class="section-title" style="top:2148px">Our Latest Blog</h2>

<div class="blog-tile" style="left:150px;top:2222px;width:292px;height:253px;background:linear-gradient(180deg,#3f6e9a,#b0a9a0 45%,#f0b060 65%,#3a2418)" role="img" aria-label="Photo of three crosses on a hill at sunrise"></div>
<div class="blog-post">
  <h3>Lorem ipsum dolor sit amet, conse ctetur adipiscing elit, sed do eius mod tempor incidi</h3>
  <p>Lorem ipsum dolor sit amet, consectetur adipiscing elit, sed do eiusmod tempor incididunt ut labore et dolore magna aliqua Ut enim ad minim.</p>
  <a class="learn-more">Learn More</a>
</div>
<div class="blog-tile" style="left:757px;top:2222px;width:293px;height:253px;background:linear-gradient(180deg,#5d7890,#c9b49a 55%,#a06a3a 80%,#6e4523)" role="img" aria-label="Photo of a camel caravan silhouetted on desert dunes"></div>
<div class="blog-tile" style="left:151px;top:2487px;width:291px;height:193px;background:radial-gradient(ellipse at 30% 40%,#f6ecc0,#8a7a5a 35%,#2e2a22)" role="img" aria-label="Photo of light shining out of an empty stone tomb"></div>
<div class="blog-tile" style="left:455px;top:2487px;width:291px;height:193px;background:linear-gradient(160deg,#8c7a70,#b9b3ad 55%,#cfcac4)" role="img" aria-label="Photo of a crown of thorns and a hammer with nails"></div>
<div class="blog-tile" style="left:758px;top:2487px;width:292px;height:193px;background:linear-gradient(100deg,#a9b0b4,#e7c28a 40%,#9a7754 70%,#2a221c)" role="img" aria-label="Photo of a silhouetted person praying at sunset"></div>

<section class="contact">
  <h2 class="section-title" style="top:72px">Get In Touch</h2>
</section>
<div class="field" style="left:228px;top:2931px;width:367px;height:43px">First name</div>
<div class="field" style="left:605px;top:2931px;width:367px;height:43px">Last name</div>
<div class="field" style="left:228px;top:2987px;width:367px;height:43px">Email</div>
<div class="field" style="left:605px;top:2987px;width:367px;height:43px">Phone</div>
<div class="field" style="left:228px;top:3041px;width:744px;height:107px">Message</div>
<a class="btn btn-submit">Submit</a>

<svg class="footer-shape" width="1200" height="563" viewBox="0 0 1200 563">
  <polygon points="0,0 600,102 1200,0 1200,563 0,563" fill="#050505"/>
</svg>

<div class="footer-links">
  <h4>Useful Links</h4>
  <ul><li>Home</li><li>About Us</li><li>Table Of Contents</li><li>References</li><li>Contact</li><li>Blog</li></ul>
</div>
<div class="footer-divider" style="left:313px"></div>
<div class="footer-brand"><span class="brand-mark"></span><span class="brand-name">HARVEST<br>PATH</span></div>
<div class="subscribe-input">Enter the Email</div>
<a class="btn btn-subscribe">Subscribe</a>
<div class="footer-divider" style="left:720px"></div>
<div class="footer-contact">
  <p>Lorem ipsum dolor sit amet, consectetur adipiscing elit, sed do eiusmod tempor incididunt ut labore et dolore magna aliqua.</p>
  <div class="contact-row" style="margin-top:28px">
    <svg width="10" height="13" viewBox="0 0 10 13"><path d="M5 0a5 5 0 0 0-5 5c0 4 5 8 5 8s5-4 5-8a5 5 0 0 0-5-5zm0 7a2 2 0 1 1 0-4 2 2 0 0 1 0 4z" fill="#fff"/></svg>
    <span>123 Lorem ipsum dolor sit amet, consec tetur adipiscing elit.</span>
  </div>
  <div class="contact-row">
    <svg width="11" height="11" viewBox="0 0 11 11"><path d="M2 0l2 2.5-1 1.3a7 7 0 0 0 4.2 4.2l1.3-1L11 9l-1.3 2C4.5 11 0 6.5 0 1.3z" fill="#fff"/></svg>
    <span>+1 888 8888 888</span>
  </div>
  <div class="contact-row">
    <svg width="12" height="9" viewBox="0 0 12 9"><rect width="12" height="9" fill="#fff"/><path d="M0 0l6 5 6-5" fill="none" stroke="#050505" stroke-width="1.2"/></svg>
    <span>info@harvestpath.org</span>
  </div>
</div>
<div class="footer-rule"></div>
<div class="footer-bottom" style="left:139px">Privacy Policy</div>
<div class="footer-bottom" style="left:518px">© 2022 All Rights Reserved</div>
<div class="footer-bottom" style="left:942px">Terms &amp; Conditions</div>

</body>
</html>
```